Business Recognition Design

We need a design for a recognition to be given to business leaders in our community.
The recognition shall be made on a brass plaque on wood panel background (picture attached, please use it as a background), and all drawing must be in vectors and only one color (black).
It should also have a logo on the top and signature on the right bottom.
The text is enclosed in DOC file.
Updates

Reason: just to be able to find the best solution

Reason: None of the suggestion is good enough. Logo in general is too big in comparison with the rest of the plate.

Industry/Entity Type

Business

Requirements
Must have
• - standard Windows font (or possibility to install the same font on Windows), as the name on the recognition shall be printed in the same font
Nice to have
• - some graphic element (in curves) representing achievements in business
- should look great :)

```html
<!DOCTYPE html>
<html lang="de">
<head>
<meta charset="utf-8">
<title>Auszeichnung – KapitalWerk</title>
<link href="https://fonts.googleapis.com/css2?family=Arimo:wght@400;700&display=swap" rel="stylesheet">
<style>
  :root {
    --wood-dark: #4a2a12;
    --wood-mid: #6e4220;
    --wood-light: #8a5630;
    --brass-deep: #b88a2a;
    --brass-mid: #d9b54a;
    --brass-light: #f4e08c;
    --brass-shine: #fbefb2;
    --ink: #111111;
    --screw-dark: #7a5a14;
    --screw-light: #f0d27a;
  }
  * { box-sizing: border-box; margin: 0; padding: 0; }
  html, body {
    width: 1200px;
    height: 920px;
    overflow: hidden;
    background: #ffffff;
  }
  .plaque {
    position: relative;
    width: 1200px;
    height: 920px;
    background: linear-gradient(135deg, var(--wood-light) 0%, var(--wood-mid) 45%, var(--wood-dark) 100%);
    font-family: "Arimo", Arial, sans-serif;
    color: var(--ink);
  }
  .brass-plate {
    position: absolute;
    left: 51px;
    top: 47px;
    width: 1100px;
    height: 832px;
    background:
      repeating-linear-gradient(90deg, rgba(255,255,255,0.05) 0 2px, rgba(0,0,0,0.03) 2px 4px),
      linear-gradient(135deg, var(--brass-deep) 0%, var(--brass-mid) 22%, var(--brass-light) 45%, var(--brass-shine) 55%, var(--brass-mid) 78%, var(--brass-deep) 100%);
    box-shadow: 0 0 0 2px rgba(90,60,10,0.5), 0 4px 10px rgba(0,0,0,0.35);
  }
  .screw {
    position: absolute;
    width: 26px;
    height: 26px;
    border-radius: 50%;
    background: radial-gradient(circle at 35% 35%, var(--screw-light) 0%, var(--brass-mid) 45%, var(--screw-dark) 100%);
    box-shadow: 0 1px 2px rgba(0,0,0,0.5);
  }
  .screw--tl { left: 29px; top: 18px; }
  .screw--tr { right: 29px; top: 18px; }
  .screw--bl { left: 29px; bottom: 18px; }
  .screw--br { right: 29px; bottom: 18px; }

  .content { position: absolute; inset: 0; text-align: center; }
  .brand-name {
    position: absolute;
    top: 118px;
    left: 0; right: 0;
    font-weight: 700;
    font-size: 44px;
    letter-spacing: 0.5px;
  }
  .brand-rule {
    position: absolute;
    top: 193px;
    left: 294px;
    width: 530px;
    height: 3px;
    background: var(--ink);
  }
  .award-title {
    position: absolute;
    top: 220px;
    left: 0; right: 0;
    font-size: 62px;
    font-weight: 400;
    letter-spacing: 1px;
  }
  .award-subtitle {
    position: absolute;
    top: 301px;
    left: 0; right: 0;
    font-size: 42px;
  }
  .award-year {
    position: absolute;
    top: 365px;
    left: 0; right: 0;
    font-size: 56px;
  }
  .recipient-label {
    position: absolute;
    top: 467px;
    left: 0; right: 0;
    font-size: 23px;
  }
  .recipient-name {
    position: absolute;
    top: 503px;
    left: 0; right: 0;
    font-size: 56px;
    font-weight: 700;
  }
  .citation {
    position: absolute;
    top: 641px;
    left: 0; right: 0;
    font-size: 21px;
    line-height: 30px;
  }
  .footer-place {
    position: absolute;
    top: 738px;
    left: 148px;
    font-size: 23px;
  }
  .footer-signature {
    position: absolute;
    top: 738px;
    left: 736px;
    font-size: 23px;
  }
</style>
</head>
<body>
  <main class="plaque">
    <section class="brass-plate">
      <span class="screw screw--tl"></span>
      <span class="screw screw--tr"></span>
      <span class="screw screw--bl"></span>
      <span class="screw screw--br"></span>

      <div class="content">
        <div class="brand-name">KapitalWerk</div>
        <div class="brand-rule"></div>
        <h1 class="award-title">AUSZEICHNUNG</h1>
        <p class="award-subtitle">als herausragendster Unternehmer</p>
        <p class="award-year">Deutschlands 2013</p>
        <p class="recipient-label">für Herrn Dipl.-Kfm.</p>
        <p class="recipient-name">Max Muster</p>
        <p class="citation">Unter der Leitung von Herr Dipl.-Kfm. Max Muster hat sich die FIRMA GmbH im Jahr<br>2013 unter den ersten 5% der größten deutschen Wirtschaftsunternehmen platziert.</p>
        <p class="footer-place">Gilching, 20. Juni 2013</p>
        <p class="footer-signature">Sabine Kellner</p>
      </div>
    </section>
  </main>
</body>
</html>
```